Etiketten für Bio Seifen
Zielgruppe
Wir stellen hochwertig 'handgemachte' Bio-Seifen her. Die Zielgruppe ist von 3-99 Jahren und zusätzlich haben wir auch noch Seife für Hunde.
Der Firmenname ist 'Verdolina'
Aufgabenstellung
Das Etikett soll Bezug auf Natur, Bio, Nachhaltigkeit nehmen. Wir stellen uns 'weiche' Aquarellfarben vor...Seife: Lavendel, Calendular, 7 Kräuter etc.
Das Etikett soll auf eine Beutelschachtel. Die Schachtel hat eine Anmaße: Breite 55mm; Höhe 120mm; Tiefe 30mm
Das Etikett soll im vorderen- und hinteren Bereich zusammenhängend geklebt werden.
Das Etikett soll eine Abmaße von: Breite 51mm; Höhe 114mm haben (Vorderseite) Rückseite gleich.
Wir möchten die Produkte auch gerne nummerieren, d.h. jede Seife hat eine Nummer die nicht zu groß dargestellt werden soll aber trotzdem gut leserlich.
Wir haben noch ein paar Bilder hochgeladen wie wir uns das ungefähr vorstellen.

```html
<!DOCTYPE html>
<html lang="de">
<head>
<meta charset="utf-8">
<title>Verdolina – Etiketten Bioseife</title>
<link rel="stylesheet" href="https://fonts.googleapis.com/css2?family=EB+Garamond:ital,wght@0,400;1,400;1,600&family=Montserrat:wght@400&family=Allura&display=swap">
<style>
  :root {
    --navy: #0b3c72;
    --white: #ffffff;
    --frame: #c9c9c9;
    --lav-1: #6a4a98; --lav-2: #8c6cb5; --lav-3: #c9b8dc;
    --cal-1: #f0a640; --cal-2: #f6c063; --cal-3: #fbe1a8;
    --herb-1: #2f9a55; --herb-2: #62b67c; --herb-3: #d7ecd8;
  }
  * { box-sizing: border-box; margin: 0; padding: 0; }
  html, body { width: 1200px; height: 800px; overflow: hidden; background: var(--white); }
  .sheet { position: relative; width: 1200px; height: 800px; }

  .label { position: absolute; top: 32px; width: 330px; height: 720px; border: 1px solid var(--frame); }
  .label--lavender { left: 32px; }
  .label--calendula { left: 434px; }
  .label--herbs { left: 835px; }

  .artwork { position: absolute; left: 14px; top: -1px; width: 301px; height: 691px; }
  .label--lavender .artwork { background: linear-gradient(160deg, var(--lav-1) 0%, var(--lav-2) 45%, var(--lav-3) 100%); }
  .label--calendula .artwork { background: linear-gradient(160deg, var(--cal-3) 0%, var(--cal-1) 45%, var(--cal-2) 100%); }
  .label--herbs .artwork { background: linear-gradient(160deg, var(--herb-1) 0%, var(--herb-2) 45%, var(--herb-3) 100%); }

  .fold-line { position: absolute; left: 14px; width: 301px; top: 300px; border-top: 1px dashed rgba(255,255,255,0.85); }

  .brand-box { position: absolute; left: 44px; top: 29px; width: 240px; height: 241px; background: var(--white); }
  .brand-frame { position: absolute; left: 0; top: 0; width: 240px; height: 241px; }
  .brand-name {
    position: absolute; left: 0; right: 0; top: 68px; text-align: center;
    font-family: "EB Garamond", serif; font-weight: 400; font-size: 46px; color: var(--navy); letter-spacing: 1px;
  }
  .brand-tagline {
    position: absolute; left: 0; right: 0; top: 141px; text-align: center;
    font-family: "EB Garamond", serif; font-style: italic; font-size: 16px; color: var(--navy);
  }
  .product-type {
    position: absolute; left: 9px; top: 202px; width: 222px; height: 29px; background: var(--navy); color: var(--white);
    font-family: "Montserrat", sans-serif; font-size: 12.5px; letter-spacing: 0.6px; line-height: 29px; text-align: center;
  }

  .leaf-icon { position: absolute; left: 149px; top: 507px; width: 36px; height: 34px; }

  .variant-box {
    position: absolute; left: 55px; top: 541px; width: 220px; height: 76px; background: var(--white);
    border: 1.5px solid var(--navy); border-radius: 4px; outline: 1px solid var(--white); box-shadow: 0 0 0 3px var(--navy);
    text-align: center; color: var(--navy);
  }
  .variant-number { font-family: "Montserrat", sans-serif; font-size: 15px; margin-top: 12px; line-height: 18px; }
  .variant-name { font-family: "EB Garamond", serif; font-style: italic; font-weight: 600; font-size: 22px; letter-spacing: 1.5px; margin-top: 5px; }

  .benefit-band {
    position: absolute; left: 14px; top: 642px; width: 301px; height: 48px; background: var(--navy); color: var(--white);
    font-family: "Allura", cursive; font-size: 25px; line-height: 48px; text-align: center;
  }
</style>
</head>
<body>
<main class="sheet">

  <section class="label label--lavender">
    <div class="artwork" role="img" aria-label="Lavendelfarbenes Aquarell mit weißen Blüten-Linienzeichnungen"></div>
    <div class="fold-line"></div>
    <div class="brand-box">
      <svg class="brand-frame" viewBox="0 0 240 241" fill="none" stroke="#0b3c72" stroke-width="1.3">
        <path d="M88 9 H230 V72"/><path d="M10 132 V194 H230 V132"/>
      </svg>
      <div class="brand-name">Verdolina</div>
      <div class="brand-tagline">Natur auf der Haut</div>
      <div class="product-type">HANDGEMACHTE BIOSEIFE</div>
    </div>
    <svg class="leaf-icon" viewBox="0 0 36 34" fill="#0b3c72"><path d="M17 34 C4 30 0 16 3 2 C14 8 20 20 17 34Z"/><path d="M20 34 C22 24 28 18 36 16 C35 26 29 33 20 34Z"/></svg>
    <div class="variant-box"><div class="variant-number">N°1</div><div class="variant-name">LAVENDEL</div></div>
    <div class="benefit-band">beruhigend &amp; entspannend</div>
  </section>

  <section class="label label--calendula">
    <div class="artwork" role="img" aria-label="Orange-gelbes Aquarell mit weißen Blüten-Linienzeichnungen"></div>
    <div class="fold-line"></div>
    <div class="brand-box">
      <svg class="brand-frame" viewBox="0 0 240 241" fill="none" stroke="#0b3c72" stroke-width="1.3">
        <path d="M88 9 H230 V72"/><path d="M10 132 V194 H230 V132"/>
      </svg>
      <div class="brand-name">Verdolina</div>
      <div class="brand-tagline">Natur auf der Haut</div>
      <div class="product-type">HANDGEMACHTE BIOSEIFE</div>
    </div>
    <svg class="leaf-icon" viewBox="0 0 36 34" fill="#0b3c72"><path d="M17 34 C4 30 0 16 3 2 C14 8 20 20 17 34Z"/><path d="M20 34 C22 24 28 18 36 16 C35 26 29 33 20 34Z"/></svg>
    <div class="variant-box"><div class="variant-number">N°2</div><div class="variant-name">CALENDULA</div></div>
    <div class="benefit-band">mild reinigend &amp; sanft pflegend</div>
  </section>

  <section class="label label--herbs">
    <div class="artwork" role="img" aria-label="Grünes Aquarell mit weißen Blüten-Linienzeichnungen"></div>
    <div class="fold-line"></div>
    <div class="brand-box">
      <svg class="brand-frame" viewBox="0 0 240 241" fill="none" stroke="#0b3c72" stroke-width="1.3">
        <path d="M88 9 H230 V72"/><path d="M10 132 V194 H230 V132"/>
      </svg>
      <div class="brand-name">Verdolina</div>
      <div class="brand-tagline">Natur auf der Haut</div>
      <div class="product-type">HANDGEMACHTE BIOSEIFE</div>
    </div>
    <svg class="leaf-icon" viewBox="0 0 36 34" fill="#0b3c72"><path d="M17 34 C4 30 0 16 3 2 C14 8 20 20 17 34Z"/><path d="M20 34 C22 24 28 18 36 16 C35 26 29 33 20 34Z"/></svg>
    <div class="variant-box"><div class="variant-number">N°3</div><div class="variant-name">7 KRÄUTER</div></div>
    <div class="benefit-band">nährend &amp; beruhigend</div>
  </section>

</main>
</body>
</html>
```